Push notification screens at app start up

We have an existing news publication app platform and are adding categories to push notifications.

We need two screens designed (each for Zorbel, Quillet and Android for a total of 6d) that show when the app is first launched.

The workflow of our app:
0. app launch screen while webservices run (no work needed)
1. information screen to the user promoting the benefits of push notification with "Next" button. (see concept attached)
2. Push categories selection screen. This will have list of category types, with on/off switch.

"Select the categories that you wish to receive occasional notices:
Breaking News (on/off switch)
Local News (on/off switch)
Sports (on/off switch)
Local Events (on/off switch)
Weather Alerts (on/off switch)
Local Deals (on/off switch)"

"Enable these categories on the next screen."
"Next" button

Background:
When I was looking around at app designs, I came across this one (http://www.plinthworks.example/design/7719034) and I really liked it. We obviously have different features on our screen, but I’d like to have this same feel. The colors used in this design are perfect.

UPDATE: I do not mean to limit your design to match the layout as the one mentioned above. Please use your creativity for the layout.

Our standard font in Helvetica Neue.

Notes:
- our app is developed for all phone devices from Zorbel 4 to Zorbel 6, so designs should be thoughtful of vertical scrolling if needed.
- our app is developed for Quillets, so we'll need designs completed as well. (We can finalize Zorbel design first, then translate the design to Quillet.)
- our app is developed for Android phones (not tablets), so we'll need designs completed as well. (We can finalize iOS design first, then translater to Android UI design guidelines).

We hope to establish a good on-going relationship with the designer for as-needed work in the future.

News

• Helvetica Neue

• Clean designs. No clutter.
• We would likely go with the standard on/off switches for both iOS and Android, but are open to small custom variations.

```html
<!DOCTYPE html>
<html lang="en">
<head>
<meta charset="utf-8">
<title>Notifications</title>
<link rel="stylesheet" href="https://fonts.googleapis.com/css2?family=Inter:wght@300;400;600;700&display=swap">
<style>
  :root {
    --screen-bg: #000000;
    --status-text: #ffffff;
    --card-top: #f2f2f2;
    --card-bottom: #dedede;
    --brand-red: #e8141c;
    --title-text: #3d3d3d;
    --body-text: #7a7a7a;
    --button-text: #ffffff;
  }
  * { box-sizing: border-box; margin: 0; padding: 0; }
  html, body {
    width: 675px;
    height: 1200px;
    overflow: hidden;
    background: var(--screen-bg);
    font-family: "Inter", "Helvetica Neue", Arial, sans-serif;
  }
  .screen {
    position: relative;
    width: 675px;
    height: 1200px;
    background: var(--screen-bg);
  }
  .status-bar {
    position: absolute;
    top: 0; left: 0; right: 0;
    height: 44px;
    color: var(--status-text);
    font-size: 21px;
    font-weight: 400;
  }
  .status-left {
    position: absolute;
    left: 12px; top: 10px;
    display: flex; align-items: center; gap: 8px;
  }
  .signal { display: flex; gap: 3px; }
  .signal span {
    width: 10px; height: 10px; border-radius: 50%;
    background: var(--status-text);
  }
  .signal span.empty { background: transparent; border: 1.5px solid var(--status-text); }
  .status-time {
    position: absolute; top: 10px; left: 0; right: 0;
    text-align: center; font-weight: 600;
  }
  .status-right {
    position: absolute; right: 12px; top: 10px;
    display: flex; align-items: center; gap: 8px;
  }
  .battery {
    width: 46px; height: 20px;
    border: 2px solid var(--status-text); border-radius: 4px;
    padding: 2px; position: relative;
  }
  .battery::before { content: ""; display: block; width: 100%; height: 100%; background: var(--status-text); border-radius: 1px; }
  .battery::after {
    content: ""; position: absolute; right: -6px; top: 5px;
    width: 3px; height: 7px; background: var(--status-text); border-radius: 0 2px 2px 0;
  }

  .info-card {
    position: absolute;
    left: 27px; top: 205px;
    width: 621px; height: 662px;
    border-radius: 18px;
    background: linear-gradient(180deg, var(--card-top), var(--card-bottom));
    text-align: center;
  }
  .badge {
    position: absolute;
    left: 50%; top: -86px;
    width: 154px; height: 154px;
    margin-left: -77px;
    border-radius: 50%;
    background: var(--brand-red);
    display: flex; align-items: center; justify-content: center;
  }
  .card-title {
    margin-top: 142px;
    font-size: 43px;
    font-weight: 600;
    color: var(--title-text);
    letter-spacing: 0.2px;
  }
  .card-body {
    margin-top: 34px;
    padding: 0 40px;
    font-size: 25px;
    line-height: 36px;
    font-weight: 300;
    color: var(--body-text);
  }
  .card-body + .card-body { margin-top: 36px; }

  .next-button {
    position: absolute;
    left: 27px; top: 916px;
    width: 621px; height: 97px;
    border-radius: 14px;
    background: var(--brand-red);
    color: var(--button-text);
    font-size: 40px;
    font-weight: 700;
    letter-spacing: 0.5px;
    display: flex; align-items: center; justify-content: center;
    border: none;
    font-family: inherit;
  }
</style>
</head>
<body>
<main class="screen">
  <header class="status-bar">
    <div class="status-left">
      <div class="signal"><span></span><span></span><span></span><span></span><span class="empty"></span></div>
      <span class="carrier">TELLA</span>
      <svg width="24" height="18" viewBox="0 0 24 18" aria-hidden="true">
        <path d="M12 17l3-3.5a4.5 4.5 0 0 0-6 0z" fill="#fff"/>
        <path d="M4.5 9.5a11 11 0 0 1 15 0" stroke="#fff" stroke-width="2.4" fill="none"/>
        <path d="M1 5.5a16 16 0 0 1 22 0" stroke="#fff" stroke-width="2.4" fill="none"/>
      </svg>
    </div>
    <div class="status-time">4:21 PM</div>
    <div class="status-right">
      <svg width="12" height="20" viewBox="0 0 12 20" aria-hidden="true">
        <path d="M1 5.5l10 9-5 4.5V1l5 4.5-10 9" stroke="#fff" stroke-width="1.8" fill="none" stroke-linejoin="round"/>
      </svg>
      <span>100%</span>
      <span class="battery"></span>
    </div>
  </header>

  <section class="info-card">
    <div class="badge">
      <svg width="96" height="80" viewBox="0 0 96 80" aria-hidden="true" fill="none" stroke="#fff" stroke-width="5" stroke-linejoin="round" stroke-linecap="round">
        <rect x="6" y="28" width="14" height="22" rx="3"/>
        <path d="M20 28 L52 14 V64 L20 50"/>
        <path d="M24 50 L30 70 H40 L36 54"/>
        <path d="M62 30 a12 12 0 0 1 0 18"/>
        <path d="M70 22 a22 22 0 0 1 0 34"/>
        <path d="M78 14 a32 32 0 0 1 0 50"/>
      </svg>
    </div>
    <h1 class="card-title">Notifications</h1>
    <p class="card-body">By enabling push notifications, you can<br>keep up to date with occasional<br>notifications related to items you care<br>about. Select the categories on the<br>next screen and then authorize the<br>push notifications.</p>
    <p class="card-body">If you ever change your mind, you can<br>adjust these options in the Settings<br>menu of this app.</p>
  </section>

  <button class="next-button" type="button">NEXT</button>
</main>
</body>
</html>
```